Infografik/ Zeitleiste für Startup
Zielgruppe
Wir sind ein Startup, das über die Seite Kalendaro.de zukünftig folgenden Service anbietet: Unternehmer können sehr flexibel (selbst) gestaltete Terminformulare erstellen und auf Ihrer Website einbinden. Kunden können dann diese Termine buchen und bekommen dann Erinnerungs-Mails und SMS.
Zielgruppe: Dienstleister wie Fotografen, Friseure, Versicherungsvertreter, Masseure, Restaurants, Arztpraxen. Also alle, die darauf angewiesen sind, dass vereinbarte Termine eingehalten werden und die die Terminvereinbarung vereinfachen wollen. Also weniger per Telefon, mehr über die eigene Website.
Kalendaro ist mit PunktWahl.com (aktuell noch Top-und-Flop.com) verknüpft. Kunden, die einen Termin wünschen, sehen die Bewertungen vorheriger Kunden. Das stärkt das Vertrauen und erhöht die Termin-Zuverlässigkeit (Verbessert die No-Show-Rate). Damit sinken auch die Werbekosten je Kunden (geringere Kosten pro Conversion).
Kalendaro.de und PunktWahl.com (aktuell noch Top-und-Flop.com) wurde vom Team von Bilder-Atelier.de entwickelt. Dank Kalendaro und PunktWahl.com haben wir (das Team von Bilder-Atelier.de) folgende Vorteile:
- verbesserte Termin-Zuverlässigkeit (No-Show-Rate)
- mehr Kunden, mehr Shootings
- höherer Umsatz
- Zeitersparnis bei der Terminvereinbarung
- Senkungen der Werbekosten je Kunden (geringere Kosten pro Conversion)
Das ist der Grund, warum wir Kalendaro und PunktWahl nun auch für andere Branchen anbieten.
Siehe auch: https://www.videoplattform.example/watch?v=Qm7Rt2Lp9Xz
Siehe auch: https://www.videoplattform.example/watch?v=Vn4Kd8Sw3Hb
Aufgabenstellung
Wir benötigen für Kalendaro.de eine Infografik. Diese soll verdeutlichen, welche Vorteile wir (Bilder-Atelier.de) dank Kalendaro und PunktWahl haben:
Der Betrachter soll diese Zahlen auf einen Blick werten und die Vorteile für SEIN GESCHÄFT erkennen können. Zum Beispiel anhand einer Zeitleiste, die die Entwicklung der verschiedenen Kennzahlen wiedergibt.
Die Kennzahlen (die Entwicklung) können Sie hier aufrufen: https://ablage.example/ordner/7KpRwZ2mNc5Qx8LtVb3HyJ6dFs9GaE1Uo?usp=sharing
Besonders soll die positive Entwicklung ab Ende September 2017 deutlich werden. Ab Ende September 2017 haben wir Kalendaro und PunktWahl.com für die Terminvereinbarung genutzt. Vorher haben wir Termine per Email und Telefon vereinbart, was deutlich zeitintensiver war.
Das Design der Zeitleiste (der Infografik) soll sich an Kalendaro.de orientieren.
Falls die sechs Kennzahlen nicht übersichtlich in einer Zeitleiste darstellbar sind, könnten die Kennzahlen auf mehrere Grafiken aufgeteilt werden.
Vorstellbar ist auch eine interaktive Infografik, bei der man die jeweilige Kennzahl auswählen kann.
Wir lassen uns hier gerne von Ihrer Kreativität überraschen. Der spätere Kunde/Nutzer/ Betrachter der Infografik steht bitte im Vordergrund jeder Überlegung/jedes Designs.
Nutzen Sie ggf. bitte Icons und verschiedenen Farben, um die verschiedenen Kennzahlen auch visuell zu verdeutlichen.
Die Infografik soll später auf https://developer.kalendaro.de/de/about-us.html und in Flyern veröffentlicht werden.
Wesentliche Funktionen und Vorteile siehe auch:
https://www.videoplattform.example/watch?v=Qm7Rt2Lp9Xz
https://www.videoplattform.example/watch?v=Vn4Kd8Sw3Hb
Die einzelnen gr..

```html
<!DOCTYPE html>
<html lang="de">
<head>
<meta charset="utf-8">
<title>Kalendaro – Kennzahlen</title>
<link href="https://fonts.googleapis.com/css2?family=Roboto:wght@300;400;500&display=swap" rel="stylesheet">
<style>
  :root {
    --bg: #ffffff;
    --green: #6cb52d;
    --green-text: #4a8a2e;
    --blue: #62c5d8;
    --blue-text: #5bbfd6;
    --rose: #f3c4c1;
    --navy-text: #3d5874;
    --magenta: #e9559b;
    --dark-text: #2a2a2a;
    --lime: #dfe12e;
    --olive: #8cba2a;
    --gold-text: #d8a257;
  }
  html, body {
    margin: 0;
    padding: 0;
    width: 1200px;
    height: 771px;
    overflow: hidden;
    background: var(--bg);
    font-family: "Roboto", Arial, sans-serif;
  }
  .stage {
    position: relative;
    width: 1386px;
    height: 890px;
    transform: scale(0.8658);
    transform-origin: 0 0;
  }
  .graphics {
    position: absolute;
    inset: 0;
    width: 1386px;
    height: 890px;
  }
  .metric {
    position: absolute;
    font-weight: 500;
    font-size: 26px;
    line-height: 34px;
    white-space: nowrap;
  }
  .metric .value-line {
    display: flex;
    align-items: baseline;
    gap: 8px;
    line-height: 54px;
  }
  .metric .value {
    font-weight: 400;
    font-size: 54px;
    letter-spacing: 0.5px;
  }
  .metric--revenue { left: 262px; top: 262px; color: var(--green-text); }
  .metric--shootings { left: 517px; top: 63px; color: var(--blue-text); }
  .metric--customers { left: 1188px; top: 176px; color: var(--navy-text); }
  .metric--noshow { left: 262px; top: 555px; color: var(--dark-text); }
  .metric--time { left: 438px; top: 634px; color: var(--dark-text); }
  .metric--adcost { left: 1212px; top: 528px; color: var(--gold-text); }
</style>
</head>
<body>
<div class="stage">
  <svg class="graphics" viewBox="0 0 1386 890" xmlns="http://www.w3.org/2000/svg">
    <defs>
      <linearGradient id="tone-money" x1="0" y1="0" x2="0" y2="1">
        <stop offset="0" stop-color="#eeeeee"/><stop offset="1" stop-color="#c9d6c4"/>
      </linearGradient>
      <linearGradient id="tone-camera" x1="0" y1="0" x2="1" y2="1">
        <stop offset="0" stop-color="#4a4a4a"/><stop offset="1" stop-color="#1b1b1b"/>
      </linearGradient>
      <linearGradient id="tone-shopper" x1="0" y1="0" x2="0" y2="1">
        <stop offset="0" stop-color="#c9a48e"/><stop offset="1" stop-color="#d58f86"/>
      </linearGradient>
      <linearGradient id="tone-worried" x1="0" y1="0" x2="0" y2="1">
        <stop offset="0" stop-color="#e36aa8"/><stop offset="1" stop-color="#f1e3dc"/>
      </linearGradient>
      <linearGradient id="tone-clock" x1="0" y1="0" x2="0" y2="1">
        <stop offset="0" stop-color="#f2f2f2"/><stop offset="1" stop-color="#dcdc8a"/>
      </linearGradient>
      <linearGradient id="tone-savings" x1="0" y1="0" x2="0" y2="1">
        <stop offset="0" stop-color="#9cc65a"/><stop offset="1" stop-color="#c99a5c"/>
      </linearGradient>
    </defs>

    <g class="arrow arrow--up" fill="var(--green)" transform="translate(60 400) rotate(-43.1)">
      <rect x="0" y="-23" width="340" height="46"/><polygon points="336,-62 431,0 336,62"/>
    </g>
    <g class="arrow arrow--up" fill="var(--blue)" transform="translate(525 360) rotate(-43.1)">
      <rect x="0" y="-23" width="340" height="46"/><polygon points="336,-62 431,0 336,62"/>
    </g>
    <g class="arrow arrow--up" fill="var(--rose)" transform="translate(945 370) rotate(-43.1)">
      <rect x="0" y="-23" width="340" height="46"/><polygon points="336,-62 431,0 336,62"/>
    </g>
    <g class="arrow arrow--down" fill="var(--magenta)" transform="translate(50 570) rotate(39.8)">
      <rect x="0" y="-25" width="338" height="50"/><polygon points="334,-66 430,0 334,66"/>
    </g>
    <g class="arrow arrow--down" fill="var(--lime)" transform="translate(500 560) rotate(42.2)">
      <rect x="0" y="-25" width="340" height="50"/><polygon points="336,-66 432,0 336,66"/>
    </g>
    <g class="arrow arrow--down" fill="var(--olive)" transform="translate(1020 545) rotate(42.2)">
      <rect x="0" y="-25" width="347" height="50"/><polygon points="343,-66 439,0 343,66"/>
    </g>

    <rect role="img" aria-label="Figur mit Taschenrechner auf Geldscheinstapeln" x="12" y="12" width="232" height="338" rx="20" fill="url(#tone-money)"/>
    <rect role="img" aria-label="Spiegelreflexkamera mit Objektiv" x="576" y="200" width="268" height="220" rx="24" fill="url(#tone-camera)"/>
    <rect role="img" aria-label="Lächelnde Kundin mit Einkaufstüten" x="995" y="35" width="178" height="355" rx="20" fill="url(#tone-shopper)"/>
    <rect role="img" aria-label="Besorgte Person mit pinken Haaren" x="12" y="525" width="236" height="320" rx="20" fill="url(#tone-worried)"/>
    <rect role="img" aria-label="Laufende Wanduhr mit Armen und Beinen" x="730" y="515" width="235" height="268" rx="30" fill="url(#tone-clock)" opacity="0.85"/>
    <rect role="img" aria-label="Pflanze wächst aus einem Glas voller Münzen" x="972" y="530" width="220" height="310" rx="20" fill="url(#tone-savings)"/>
  </svg>

  <div class="metric metric--revenue">
    <div>Umsatz</div>
    <div class="value-line">auf <span class="value">130%</span></div>
    <div>gesteigert!</div>
  </div>

  <div class="metric metric--shootings">
    <div>Foto-Shootings</div>
    <div class="value-line">auf <span class="value">180%</span></div>
    <div>gesteigert!</div>
  </div>

  <div class="metric metric--customers">
    <div>Kundenanzahl</div>
    <div class="value-line">auf <span class="value">190%</span></div>
    <div>gesteigert!</div>
  </div>

  <div class="metric metric--noshow">
    <div>No-Show-Rate</div>
    <div class="value-line">um <span class="value">65%</span></div>
    <div>abgesenkt!</div>
  </div>

  <div class="metric metric--time">
    <div>Zeitaufwand für</div>
    <div>Terminvereinbarungen</div>
    <div class="value-line">um <span class="value">80%</span></div>
    <div>abgesenkt!</div>
  </div>

  <div class="metric metric--adcost">
    <div>Werbekosten</div>
    <div>je Kunde</div>
    <div class="value-line">um <span class="value">30%</span></div>
    <div>abgesenkt!</div>
  </div>
</div>
</body>
</html>
```